Business Card Design Project

Business card based on attached logo

Todd Merrick
Todd@lorvantest.com
877-514-9073 ext. 318
Www.LorvanTest.com

Industry/Entity Type

Business

```html
<!DOCTYPE html>
<html lang="en">
<head>
<meta charset="utf-8">
<title>LorvanTest Business Cards</title>
<link rel="stylesheet" href="https://fonts.googleapis.com/css2?family=Arimo:wght@400;700&display=swap">
<style>
  :root {
    --board: #8b8d90;
    --white: #ffffff;
    --ink: #231f20;
    --red: #e31e26;
    --red-deep: #c4242b;
    --charcoal: #2a2a2a;
    --charcoal-dark: #1b1b1b;
    --font: "Arimo", Arial, sans-serif;
  }
  * { margin: 0; padding: 0; box-sizing: border-box; }
  html, body { width: 1200px; height: 720px; overflow: hidden; }
  body { background: var(--board); font-family: var(--font); position: relative; }

  .card { position: absolute; width: 564px; height: 322px; overflow: hidden; }
  .card--front  { left: 26px;  top: 26px;  background: var(--white); outline: 1px solid #6d6f72; }
  .card--red    { left: 612px; top: 26px;  background: linear-gradient(120deg, #e5262d 0%, var(--red-deep) 100%); }
  .card--white  { left: 26px;  top: 374px; background: var(--white); outline: 1px solid #6d6f72; }
  .card--dark   { left: 612px; top: 374px; background: radial-gradient(ellipse at 50% 40%, #3c3c3c 0%, var(--charcoal) 45%, var(--charcoal-dark) 100%); }

  .brand { position: absolute; display: flex; align-items: flex-start; gap: 6px; }
  .brand__name { font-weight: 700; letter-spacing: -1px; line-height: 1; }
  .brand__square { width: 22px; height: 22px; background: var(--red); }

  .card--front .brand { left: 30px; top: 104px; }
  .card--front .brand__name { font-size: 44px; color: var(--ink); }

  .divider { position: absolute; left: 297px; top: 62px; width: 1px; height: 138px; background: #cfcfcf; }

  .contact { position: absolute; left: 312px; top: 92px; }
  .contact__name { font-size: 19px; color: var(--red); letter-spacing: 0.3px; margin-bottom: 18px; margin-left: 7px; }
  .contact__line { display: flex; align-items: center; gap: 7px; font-size: 17px; color: var(--ink); margin-bottom: 10px; }
  .contact__icon { width: 14px; height: 14px; flex: none; }

  .wave { position: absolute; left: 0; bottom: 0; width: 564px; height: 80px; }

  .web { position: absolute; font-size: 16px; letter-spacing: 2.6px; }
  .card--front .web { left: 38px; top: 286px; color: var(--white); }
  .card--red .web   { left: 36px; top: 292px; color: var(--white); }
  .card--white .web, .card--dark .web { left: 0; right: 0; top: 282px; text-align: center; }
  .card--white .web { color: var(--ink); }
  .card--dark .web  { color: var(--white); }

  .card--red .brand { left: 34px; top: 40px; }
  .card--red .brand__name { font-size: 74px; color: var(--white); }
  .card--red .brand__square { background: var(--white); }
  .faint-square { position: absolute; left: 492px; top: 152px; width: 90px; height: 90px; background: rgba(255,255,255,0.14); }

  .card--white .brand, .card--dark .brand { left: 0; right: 0; top: 118px; justify-content: center; }
  .card--white .brand__name { font-size: 64px; color: var(--ink); }
  .card--dark .brand__name { font-size: 64px; color: var(--white); }
  .card--dark .brand__square { background: var(--white); }
</style>
</head>
<body>

<section class="card card--front">
  <div class="brand">
    <span class="brand__name">LorvanTest</span>
    <span class="brand__square"></span>
  </div>
  <div class="divider"></div>
  <div class="contact">
    <p class="contact__name">TODD MERRICK</p>
    <p class="contact__line">
      <svg class="contact__icon" viewBox="0 0 16 16" aria-hidden="true">
        <circle cx="8" cy="8" r="7" fill="none" stroke="#e31e26" stroke-width="1.4"/>
        <path d="M5.5 4.5c.6-.4 1.2 0 1.4.6l.3 1c.1.4-.1.7-.4.9l-.3.2c.4 1 1.1 1.8 2 2.3l.3-.3c.3-.3.6-.3.9-.2l1 .4c.5.2.8.8.4 1.4-.5.7-1.4.9-2.2.5-2-.9-3.5-2.6-4.1-4.7-.2-.8.1-1.6.7-2.1z" fill="#e31e26"/>
      </svg>
      877-514-9073 ext. 318
    </p>
    <p class="contact__line">
      <svg class="contact__icon" viewBox="0 0 16 16" aria-hidden="true">
        <rect x="1" y="3.5" width="14" height="9" rx="1" fill="#e31e26"/>
        <path d="M1.5 4.2 8 9l6.5-4.8" fill="none" stroke="#fff" stroke-width="1.2"/>
      </svg>
      Todd@lorvantest.com
    </p>
  </div>
  <svg class="wave" viewBox="0 0 564 80" preserveAspectRatio="none" aria-hidden="true">
    <path d="M0 28 C120 -2 250 8 340 34 C430 58 510 40 564 8 L564 80 L0 80 Z" fill="#e31e26"/>
    <path d="M0 32 C120 4 250 14 340 40 C430 64 510 46 564 16 L564 80 L0 80 Z" fill="#ffffff"/>
    <path d="M0 36 C120 10 250 20 340 46 C430 68 510 52 564 26 L564 80 L0 80 Z" fill="#2a2a2a"/>
    <path d="M300 34 C390 56 480 52 564 28 L564 34 C480 60 390 64 300 34 Z" fill="#e31e26"/>
  </svg>
  <p class="web">www.lorvantest.com</p>
</section>

<section class="card card--red">
  <div class="brand">
    <span class="brand__name">LorvanTest</span>
  </div>
  <div class="faint-square"></div>
  <p class="web">www.lorvantest.com</p>
</section>

<section class="card card--white">
  <div class="brand">
    <span class="brand__name">LorvanTest</span>
    <span class="brand__square"></span>
  </div>
  <p class="web">www.lorvantest.com</p>
</section>

<section class="card card--dark">
  <div class="brand">
    <span class="brand__name">LorvanTest</span>
    <span class="brand__square"></span>
  </div>
  <p class="web">www.lorvantest.com</p>
</section>

</body>
</html>
```